Coastline Premier Retreats Business Card Design

Design a business card for Coastline Premier Retreats. Look at the website for colors and reference. Card should have logo, name, title, office number, mobile number, email, URL and a tagline like, "Luxury Hotel & Resort Email Marketing" (This might change).

https://www.coastlinepremierretreats.example

The rest I will leave up to your imagination.

Contact Information for Business Card

Logo, name, title, office number, mobile number, email, URL and a tagline like, "Luxury Hotel & Resort Email Marketing" (This might change).

```html
<!DOCTYPE html>
<html lang="en">
<head>
<meta charset="utf-8">
<title>Coastline Premier Retreats Business Card</title>
<link href="https://fonts.googleapis.com/css2?family=Open+Sans:wght@400;600;700&display=swap" rel="stylesheet">
<style>
  :root {
    --backdrop: #3b3b3b;
    --card: #1b1b1b;
    --accent: #f07a1e;
    --text-light: #e6e6e6;
    --text-muted: #5a5a5a;
  }
  * { margin: 0; padding: 0; box-sizing: border-box; }
  html, body {
    width: 1200px; height: 801px; overflow: hidden;
    background: var(--backdrop);
    font-family: "Open Sans", Arial, sans-serif;
  }
  .canvas { position: relative; width: 1200px; height: 801px; }
  .card {
    position: absolute; top: 250px;
    width: 520px; height: 297px;
    background: var(--card);
    border-bottom: 3px solid var(--accent);
    box-shadow: 0 10px 30px rgba(0,0,0,.35);
  }
  .card-front { left: 50px; }
  .card-back { left: 630px; }

  .brand {
    position: absolute; left: 36px; top: 98px;
    display: flex; align-items: center; gap: 10px;
  }
  .brand-mark { width: 14px; height: 14px; background: var(--accent); }
  .brand-name {
    color: var(--text-light); font-weight: 700;
    font-size: 17px; letter-spacing: .5px; text-transform: uppercase;
    line-height: 1.15; width: 180px;
  }
  .divider {
    position: absolute; left: 250px; top: 58px;
    width: 1px; height: 128px; background: var(--accent);
  }
  .contact { position: absolute; left: 272px; top: 52px; }
  .person-name {
    color: var(--accent); font-weight: 700; font-size: 17px;
    text-transform: uppercase; letter-spacing: .3px;
  }
  .person-title { color: var(--text-light); font-size: 12px; margin-bottom: 14px; }
  .contact-line {
    display: flex; align-items: center; gap: 8px;
    color: var(--text-light); font-size: 11.5px; line-height: 20px;
  }
  .contact-line svg { width: 11px; height: 11px; fill: var(--accent); flex: none; }
  .tagline {
    position: absolute; left: 0; right: 0; bottom: 42px;
    text-align: center; color: var(--text-light); font-size: 12.5px;
  }
  .back-brand {
    position: absolute; inset: 0;
    display: flex; align-items: center; justify-content: center; gap: 12px;
  }
  .back-brand .brand-mark { width: 18px; height: 18px; background: var(--text-muted); }
  .back-brand .brand-name {
    color: var(--text-muted); font-size: 26px; width: auto; letter-spacing: 1px;
  }
</style>
</head>
<body>
<main class="canvas">
  <section class="card card-front">
    <div class="brand">
      <span class="brand-mark"></span>
      <span class="brand-name">Coastline Premier Retreats</span>
    </div>
    <div class="divider"></div>
    <div class="contact">
      <p class="person-name">Dorian Vale</p>
      <p class="person-title">President / CEO</p>
      <p class="contact-line">
        <svg viewBox="0 0 24 24"><path d="M6.6 10.8a15 15 0 0 0 6.6 6.6l2.2-2.2a1 1 0 0 1 1-.25 11.4 11.4 0 0 0 3.6.57 1 1 0 0 1 1 1V20a1 1 0 0 1-1 1A17 17 0 0 1 3 4a1 1 0 0 1 1-1h3.5a1 1 0 0 1 1 1c0 1.25.2 2.45.57 3.57a1 1 0 0 1-.25 1z"/></svg>
        555.014.2200
      </p>
      <p class="contact-line">
        <svg viewBox="0 0 24 24"><path d="M2 5h20v14H2z M2 5l10 8 10-8" /></svg>
        info@coastlinepremierretreats.example
      </p>
      <p class="contact-line">
        <svg viewBox="0 0 24 24"><circle cx="12" cy="12" r="10"/></svg>
        www.coastlinepremierretreats.example
      </p>
    </div>
    <p class="tagline">Luxury Hotel &amp; Resort Email Marketing</p>
  </section>

  <section class="card card-back">
    <div class="back-brand">
      <span class="brand-mark"></span>
      <span class="brand-name">Coastline Premier Retreats</span>
    </div>
  </section>
</main>
</body>
</html>
```